VKT Consulting

Government/Entitlement Consulting Services- I assist developers obtain entitlements from local, state and federal government agencies so that they can build their projects. Often these projects are very complicated and political and may face community opposition.

Target Market(s)

Real Estate Developers

Industry/Entity Type

Business Consultant

Contact Information for Business Card

Dana Melbrook
Principal

Font styles to use
Serif
Sans Serif

Requirements
Must have
• Classy and professional appeal.
Nice to have
• I like a combination of a mat and glossy finish. I've seen that done with black and then a bold color for a pop, but am not 100% committed to that.

```html
<!DOCTYPE html>
<html lang="en">
<head>
<meta charset="utf-8">
<title>VKT Consulting – Business Card</title>
<link rel="stylesheet" href="https://fonts.googleapis.com/css2?family=Open+Sans:wght@400;600;700&display=swap">
<style>
  :root {
    --bg-top: #a3a3a3;
    --bg-bottom: #878787;
    --card-white: #ffffff;
    --navy: #0a1451;
    --navy-deep: #020f52;
    --text-grey: #555a60;
    --white: #ffffff;
  }
  * { margin: 0; padding: 0; box-sizing: border-box; }
  html, body { width: 1200px; height: 900px; overflow: hidden; }
  body {
    position: relative;
    background: linear-gradient(to bottom, var(--bg-top), var(--bg-bottom));
    font-family: "Open Sans", sans-serif;
  }
  .card {
    position: absolute;
    top: 306px;
    width: 440px;
    height: 271px;
    border-radius: 12px;
    overflow: hidden;
  }
  .card--front { left: 149px; background: var(--card-white); }
  .card--back { left: 608px; background: var(--navy-deep); }

  .wordmark {
    position: absolute;
    font-family: "Open Sans", sans-serif;
    font-weight: 700;
    line-height: 1;
  }
  .wordmark span { display: block; }
  .wordmark__short { letter-spacing: 1px; }
  .wordmark__long { letter-spacing: 0.5px; }

  .card--front .wordmark { left: 38px; top: 90px; color: var(--navy); }
  .card--front .wordmark__short { font-size: 60px; }
  .card--front .wordmark__long { font-size: 25px; margin-top: 8px; }

  .card--back .wordmark { left: 121px; top: 84px; color: var(--white); }
  .card--back .wordmark__short { font-size: 70px; }
  .card--back .wordmark__long { font-size: 29px; margin-top: 9px; }

  .contact {
    position: absolute;
    left: 243px;
    top: 69px;
    color: var(--text-grey);
    font-size: 12px;
    line-height: 15.5px;
  }
  .contact__name { color: var(--navy); font-weight: 700; font-size: 14.5px; line-height: 18px; }
  .contact__title { margin-bottom: 10px; }
  .contact__address { margin-bottom: 10px; }
  .contact__list { list-style: none; }
  .contact__list li { display: flex; align-items: center; gap: 7px; height: 16px; }
  .contact__list svg { width: 9px; height: 9px; flex: none; fill: var(--navy); }
</style>
</head>
<body>
  <section class="card card--front">
    <div class="wordmark">
      <span class="wordmark__short">VKT</span>
      <span class="wordmark__long">CONSULTING</span>
    </div>
    <div class="contact">
      <p class="contact__name">Dana Melbrook</p>
      <p class="contact__title">Managing Director</p>
      <p class="contact__address">4820 Harbor Ridge Lane<br>Westfield, 204518.</p>
      <ul class="contact__list">
        <li>
          <svg viewBox="0 0 10 10" aria-hidden="true"><path d="M2 0.5 L3.6 2.6 L2.7 3.7 Q3.6 5.9 6.3 7.3 L7.4 6.4 L9.5 8 L8.4 9.5 Q4.5 9.2 1.8 6 Q0.2 3.6 0.6 1.6 Z"/></svg>
          <span>044-555 218 407</span>
        </li>
        <li>
          <svg viewBox="0 0 10 10" aria-hidden="true"><path d="M0.5 2 H9.5 V8.2 H0.5 Z M1 2.5 L5 5.5 L9 2.5" stroke="#fff" stroke-width="0.8"/></svg>
          <span>info@vktconsult.com</span>
        </li>
        <li>
          <svg viewBox="0 0 10 10" aria-hidden="true"><circle cx="5" cy="5" r="4.5"/></svg>
          <span>www.vktconsult.com</span>
        </li>
      </ul>
    </div>
  </section>

  <section class="card card--back">
    <div class="wordmark">
      <span class="wordmark__short">VKT</span>
      <span class="wordmark__long">CONSULTING</span>
    </div>
  </section>
</body>
</html>
```